Irrigation Business needs their business cards modernised and revamped

I would like to keep my current logo, colours and revamp the format of the card.

I would like the card to be clean yet important.

Im not sure if you include texture but i would like the named logo to be indented into the card etc.

show me something alive and free something thats clinical to the point yet has a feel of achievement. i would like people to go nice card.

Target Market(s)

high end clients, corporate, sports field manger, the guys that make the decisions

Industry/Entity Type

Business

Contact Information for Business Card

nformation to be included

Dean Harlow (Director)
0487305526
dean@kolvat.biz
www.kestonfieldworks.com

instagram logo
google logo
facebook logo

Colors

Designer to choose colors to be used in the design.

Requirements
Nice to have
• indentations a really nice feel to the card good texture

```html
<!DOCTYPE html>
<html lang="en">
<head>
<meta charset="utf-8">
<title>Keston Fieldworks – Business Card</title>
<link href="https://fonts.googleapis.com/css2?family=Roboto:wght@400;500;700&family=Roboto+Condensed:wght@500;700&display=swap" rel="stylesheet">
<style>
  :root {
    --backdrop: #2b2b2b;
    --paper: #f2f2f2;
    --brand-blue: #2f63a8;
    --sky-blue: #2ea3d0;
    --back-blue: #3d6faa;
    --white: #ffffff;
    --rule: rgba(255,255,255,0.45);
  }
  html, body {
    margin: 0;
    padding: 0;
    width: 1200px;
    height: 960px;
    overflow: hidden;
    background: var(--backdrop);
  }
  .canvas {
    position: relative;
    width: 1200px;
    height: 960px;
  }
  .card {
    position: absolute;
    width: 600px;
    height: 343px;
    overflow: hidden;
    box-shadow: 0 4px 10px rgba(0,0,0,0.45);
  }
  .card--front {
    left: 314px;
    top: 113px;
    background: var(--paper);
  }
  .card--back {
    left: 311px;
    top: 472px;
    background: var(--back-blue);
  }

  /* front: brand mark */
  .brand {
    position: absolute;
    left: 33px;
    top: 31px;
    display: flex;
    flex-direction: column;
    align-items: center;
    gap: 10px;
  }
  .brand__dot {
    width: 70px;
    height: 70px;
    border-radius: 50%;
    background: var(--sky-blue);
  }
  .brand__name {
    font-family: "Roboto", sans-serif;
    font-weight: 700;
    font-size: 21px;
    letter-spacing: 0.2px;
    color: var(--brand-blue);
    white-space: nowrap;
  }

  /* front: contact band */
  .contact-band {
    position: absolute;
    left: 0;
    top: 173px;
    width: 600px;
    height: 147px;
    background: var(--sky-blue);
  }
  .contact-band__accent {
    position: absolute;
    right: 0;
    top: 0;
    width: 134px;
    height: 147px;
    background: var(--brand-blue);
  }
  .person {
    position: absolute;
    left: 33px;
    top: 16px;
    color: var(--white);
  }
  .person__name {
    font-family: "Roboto Condensed", sans-serif;
    font-weight: 500;
    font-size: 21px;
    margin: 0;
    line-height: 1.1;
  }
  .person__role {
    font-family: "Roboto", sans-serif;
    font-weight: 500;
    font-size: 15px;
    margin: 6px 0 0;
  }
  .contact-list {
    list-style: none;
    margin: 14px 0 0;
    padding: 0;
    font-family: "Roboto", sans-serif;
    font-size: 14px;
    line-height: 19px;
  }
  .contact-list li {
    display: flex;
    align-items: center;
    gap: 8px;
  }
  .contact-list svg {
    width: 13px;
    height: 13px;
    fill: var(--white);
    flex: none;
  }

  /* back */
  .back-brand {
    position: absolute;
    left: 0;
    top: 80px;
    width: 600px;
    display: flex;
    flex-direction: column;
    align-items: center;
    gap: 18px;
  }
  .back-brand__ring {
    width: 100px;
    height: 100px;
    border-radius: 50%;
    border: 3px solid var(--white);
    box-sizing: border-box;
  }
  .back-brand__name {
    font-family: "Roboto", sans-serif;
    font-weight: 700;
    font-size: 31px;
    color: var(--white);
    white-space: nowrap;
  }
  .social-row {
    position: absolute;
    left: 50px;
    top: 291px;
    width: 500px;
    height: 28px;
    display: flex;
    align-items: center;
    gap: 4px;
  }
  .social-row__rule {
    flex: 1;
    height: 1px;
    background: linear-gradient(90deg, transparent, var(--rule));
  }
  .social-row__rule--right {
    background: linear-gradient(90deg, var(--rule), transparent);
  }
  .social-row__dot {
    width: 27px;
    height: 27px;
    border-radius: 50%;
    background: var(--white);
  }
</style>
</head>
<body>
<main class="canvas">

  <section class="card card--front">
    <div class="brand">
      <div class="brand__dot"></div>
      <div class="brand__name">KESTON FIELDWORKS</div>
    </div>

    <div class="contact-band">
      <div class="person">
        <h1 class="person__name">DEAN HARLOW</h1>
        <p class="person__role">DIRECTOR</p>
        <ul class="contact-list">
          <li>
            <svg viewBox="0 0 24 24" aria-hidden="true"><path d="M6.6 10.8c1.4 2.8 3.8 5.1 6.6 6.6l2.2-2.2c.3-.3.7-.4 1-.2 1.1.4 2.3.6 3.6.6.6 0 1 .4 1 1V20c0 .6-.4 1-1 1C10.6 21 3 13.4 3 4c0-.6.4-1 1-1h3.5c.6 0 1 .4 1 1 0 1.3.2 2.5.6 3.6.1.3 0 .7-.2 1z"/></svg>
            0487305526
          </li>
          <li>
            <svg viewBox="0 0 24 24" aria-hidden="true"><path d="M2 5h20v14H2z M2 5l10 8 10-8" fill="none" stroke="#fff" stroke-width="2"/></svg>
            dean@kolvat.biz
          </li>
          <li>
            <svg viewBox="0 0 24 24" aria-hidden="true"><circle cx="12" cy="12" r="10"/><path d="M2 12h20M12 2c3 3 3 17 0 20M12 2c-3 3-3 17 0 20" fill="none" stroke="#2ea3d0" stroke-width="1.5"/></svg>
            www.kestonfieldworks.com
          </li>
        </ul>
      </div>
      <div class="contact-band__accent"></div>
    </div>
  </section>

  <section class="card card--back">
    <div class="back-brand">
      <div class="back-brand__ring"></div>
      <div class="back-brand__name">KESTON FIELDWORKS</div>
    </div>
    <div class="social-row">
      <span class="social-row__rule"></span>
      <span class="social-row__dot"></span>
      <span class="social-row__dot"></span>
      <span class="social-row__dot"></span>
      <span class="social-row__rule social-row__rule--right"></span>
    </div>
  </section>

</main>
</body>
</html>
```